Home Page Design (PSD Only) - Ecommerce - Yarn, Apparel and Socks

We need a new home page design for our e-commerce site WoolHarbor.com.
Our team will create the HTML/CSS using the Scaffoldy framework. We just need the final PSD and slices. Our brand/logo will remain however our focus has shifted to two key product categories. 1: Yarn 2: Socks. We also sell products in the other categories but these will not be the focus and jewelry will likely go away.

Our socks and yarn are focused on "Affordable Luxury" We carry over 2000 yarns (Huge Selection) and have the largest selection on the internet for Alpaca Socks.

Our buyers are very different. Most yarn buyers are women 25-55 who are very tactile. They want to feel the yarn so this somehow needs to come through. Clean and Warm, Affordable Luxury.

Our sock buyers buy premium socks ($15-20/pair) are split male/female and have little interest in Yarn or Knitting. I realize we should likely have 2 different sites but we've spent 7 years building the brand and have loyalty from both markets and are not getting x-sell. Especially knitters who buy our socks and stuffed bears, etc for gifts.

We'll be moving toward a new responsive design based on the Scaffoldy framework under the hood.
Updates

Project Deadline Extended
Reason: Requested by some designers to make additional changes.

Project Deadline Extended
Reason: We received more feedback from customers so need to get this feedback to designers.

Target Market(s)

Women for the Yarn (knitters). Split 60F/40M for socks
Current site is blue. Feel free to update the colors to make the site more attractive for women.

Industry/Entity Type

E-Commerce

Requirements
Must have
• Rotating Hero, Global Search, Must incorporate our blue logo (or inverse). Social bar for Chirpline, Friendwall, Clipboardia, Loopmeet (yarn social site), Stitchspark (yarn social site).
Can use warm colors to appeal more to women.
Must support a responsive design (scaffoldy)
Nice to have
• Site should resonate with Knitters but not alienate users who just come to shop for Socks, Stuffed Bears, Sweaters, etc.
Clean, simple design, but with warmth and upscale feeling.
Yarn sites: fibrebarn.example, loomcrate.example
Sock/Apparel Sites: toastytoes.example, stridewell.example, cedarvale.example, tuv.example

I've added some initial comps that tested OK but early feedback was it was too plain and lacked emotional appeal.

```html
<!DOCTYPE html>
<html lang="en">
<head>
<meta charset="utf-8">
<title>WoolHarbor – Home</title>
<link href="https://fonts.googleapis.com/css2?family=Ubuntu:wght@300;400;500;700&family=Varela+Round&display=swap" rel="stylesheet">
<style>
:root{
  --brown:#8b6a4b;
  --brown-dark:#6e5238;
  --cream:#fbeedd;
  --cream-deep:#f1d9bc;
  --page:#f4f6fa;
  --ink:#3f3a36;
  --muted:#8e8e8e;
  --blue:#6c9fd5;
  --amber:#c98b45;
  --green:#6aaa3e;
  --link:#4a95cf;
  --stripe:#f4e886;
}
*{box-sizing:border-box;margin:0;padding:0}
html,body{width:1152px;height:1200px;overflow:hidden}
body{position:relative;background:var(--page);font-family:"Ubuntu",sans-serif;color:var(--ink)}
.abs{position:absolute}
a{color:inherit;text-decoration:none}

.site-header{left:0;top:0;width:1152px;height:106px;background:var(--brown)}
.brand{left:127px;top:26px;display:flex;align-items:center;gap:10px;color:#fff;font-size:36px;font-weight:500;letter-spacing:.5px}
.brand-dot{width:30px;height:30px;border-radius:50%;background:#fff}
.account-links{right:126px;top:9px;color:#fff;font-size:12.5px;font-weight:500}
.account-links span{margin:0 4px}
.follow{left:843px;top:73px;color:#fff;font-size:15px;font-weight:500}
.social{top:69px;width:24px;height:24px;border-radius:3px}
.social.s1{left:929px;background:#4f6eb0}
.social.s2{left:967px;background:#e9e6e0}
.social.s3{left:998px;background:#5fb7e5}

.main-nav{left:105px;top:106px;width:942px;height:47px;background:linear-gradient(#fcf1e3,var(--cream-deep));border-radius:0 0 4px 4px;box-shadow:0 1px 2px rgba(0,0,0,.12)}
.main-nav a{position:absolute;top:15px;font-size:14.5px;color:var(--brown)}
.main-nav a.current{color:#3d2f22;font-weight:500}
.search{left:687px;top:8px;width:254px;height:32px;background:#fff;border-radius:2px;font-size:12.5px;color:#aaa;padding:9px 12px}
.search svg{position:absolute;right:10px;top:8px}

.hero{left:106px;top:176px;width:940px;height:459px;background:
  radial-gradient(circle at 70% 40%,#3a5fa2 0,transparent 30%),
  radial-gradient(circle at 90% 25%,#2c9a8e 0,transparent 30%),
  radial-gradient(circle at 62% 85%,#6a4aa0 0,transparent 28%),
  radial-gradient(circle at 50% 8%,#e46a4a 0,transparent 25%),
  radial-gradient(circle at 95% 80%,#1f9b8d 0,transparent 30%),
  linear-gradient(90deg,#e0a24a,#d96a48 40%,#3f6eaa 70%,#2aa092);box-shadow:0 1px 3px rgba(0,0,0,.2)}
.promo{left:135px;top:235px;width:418px;height:351px;border:14px solid var(--stripe);background:#fff;text-align:center}
.promo-big{position:absolute;left:86px;top:6px;font-family:"Varela Round",sans-serif;font-size:128px;line-height:1;color:var(--blue);letter-spacing:-6px}
.promo-pct{position:absolute;left:246px;top:12px;font-family:"Varela Round",sans-serif;font-size:70px;color:var(--blue);line-height:1}
.promo-off{position:absolute;left:245px;top:90px;font-family:"Varela Round",sans-serif;font-size:34px;color:var(--blue)}
.promo-title{position:absolute;left:0;width:100%;top:140px;font-size:37px;font-weight:700;line-height:42px;color:var(--amber);letter-spacing:-1.5px}
.promo-copy{position:absolute;left:20px;width:350px;top:236px;font-size:11.5px;line-height:18px;color:#555}
.promo-btn{position:absolute;left:64px;top:273px;width:263px;height:37px;background:linear-gradient(#f6e6d3,#ecd3b6);border-radius:4px;font-size:15px;font-weight:500;color:#4a3a2a;line-height:37px}

.dots{left:532px;top:658px;display:flex;gap:8px}
.dots i{width:11px;height:11px;border-radius:50%;background:#b8b8b8;box-shadow:inset 0 1px 2px rgba(0,0,0,.35)}
.dots i.on{background:#777}

.section-title{font-size:23px;font-weight:400;color:#454040;letter-spacing:.3px}
.section-sub{font-size:15.5px;color:#555;font-weight:300}
.welcome{left:124px;top:680px;width:430px}
.welcome .section-sub{margin-top:10px}
.welcome p{margin-top:9px;font-size:12.5px;line-height:21px;color:#9a9a9a;font-weight:300}
.welcome p a{color:var(--link);margin-left:10px}
.divider{left:575px;top:697px;width:1px;height:146px;background:#dcdcdc}
.products{left:612px;top:680px;width:420px}
.products .section-title{font-size:19px}
.products .section-sub{margin-top:12px}
.arrow{top:780px}
.product-tile{top:742px;width:195px;height:101px;border:1px solid #d6d6d6}
.tile-socks{left:613px;background:linear-gradient(90deg,#f0f0f0,#c4c4c4 60%,#8a8a8a)}
.tile-socks span{position:absolute;left:15px;top:10px;font-size:25px;font-style:italic;line-height:24px;color:#222;font-weight:300}
.tile-yarn{left:810px;background:radial-gradient(circle at 60% 50%,#4a6fb8 0,#c94a3a 25%,#e8c43a 38%,#f4f4f4 60%)}

.footer{left:0;top:857px;width:1152px;height:301px;background:#fff;border-top:1px solid #e2e2e2}
.fcol{top:885px}
.fcol h3{font-size:14.5px;font-weight:400;color:#333;margin-bottom:10px;letter-spacing:.3px}
.fcol li{list-style:none;font-size:12.5px;line-height:19.2px;color:#8a8a8a}
.fcol h3.gap{margin-top:24px}
.fb-title{font-size:13px;color:var(--green);margin-bottom:6px}
.fb-text{font-size:10.5px;line-height:15.5px;color:#a0a0a0;width:190px}
.fb-tag{font-size:10.5px;color:var(--link);margin-bottom:10px}
.badge{top:1080px;border-radius:3px}

.copyright{left:0;top:1158px;width:1152px;height:42px;background:linear-gradient(#a77a4e,#93683f);color:#fff;font-size:12.5px;text-align:center;line-height:44px;border-top:2px solid #7c5634}
</style>
</head>
<body>

<header class="site-header abs">
  <div class="brand abs"><span>WoolHarbor</span><span class="brand-dot"></span></div>
  <div class="account-links abs">My Account <span>|</span> View Shopping Bag &nbsp;(0 items ) <span>|</span>Go to Checkout</div>
  <div class="follow abs">Follow Us</div>
</header>
<a class="social s1 abs" aria-label="Friendwall"></a>
<a class="social s2 abs" aria-label="Clipboardia"></a>
<a class="social s3 abs" aria-label="Chirpline"></a>

<nav class="main-nav abs">
  <a class="current" style="left:20px">Home</a>
  <a style="left:85px">Yarn &amp; Fiber</a>
  <a style="left:186px">Socks</a>
  <a style="left:250px">Clothing</a>
  <a style="left:329px">Home Goods</a>
  <a style="left:437px">Jewelry</a>
  <a style="left:511px">Clearance</a>
  <a style="left:601px">Contact Us</a>
  <div class="search abs">Search
    <svg width="16" height="16" viewBox="0 0 16 16"><circle cx="6.5" cy="6.5" r="4.8" fill="none" stroke="#888" stroke-width="1.8"/><line x1="10" y1="10" x2="14.5" y2="14.5" stroke="#888" stroke-width="2.2" stroke-linecap="round"/></svg>
  </div>
</nav>

<section class="hero abs" role="img" aria-label="Close-up photo of colourful yarn balls in orange, blue, teal and purple"></section>
<div class="promo abs">
  <div class="promo-big">30</div>
  <div class="promo-pct">%</div>
  <div class="promo-off">OFF</div>
  <div class="promo-title">YARN,<br>SOCKS, SEATERS</div>
  <div class="promo-copy">LOREM IPSUM DOLOR SIT AMET, SECTETUER ADIPISCING ELIT, SED DIAM NIBUISMOD TINCIDUNT.</div>
  <a class="promo-btn">ENTENDA COMO FUNCIONAMOS</a>
</div>
<div class="dots abs"><i class="on"></i><i></i><i></i><i></i><i></i></div>

<section class="welcome abs">
  <h2 class="section-title">WELCOME TO WOOLHARBOR</h2>
  <div class="section-sub">Stylish and sophisticated italian designer Kitchens</div>
  <p>Lorem ipsum dolor sit amet, consectetuer adipiscing elit, sed diam non-ummy nibh euismod tincidunt laoreet quam erat volutpat. Ut wisi enim ad minim veniam, quis nostrud exerci tation ullamcorper suscipit lobortis nisl ut aliquip ex &nbsp;commod.<a>View Detail</a></p>
</section>
<div class="divider abs"></div>
<section class="products abs">
  <h2 class="section-title">OUR PRODUCTS</h2>
  <div class="section-sub">Stylish and sophisticated italian designer Kitchens</div>
</section>
<svg class="arrow abs" style="left:588px" width="12" height="20" viewBox="0 0 12 20"><polyline points="10,2 2,10 10,18" fill="none" stroke="#999" stroke-width="2"/></svg>
<svg class="arrow abs" style="left:1010px" width="12" height="20" viewBox="0 0 12 20"><polyline points="2,2 10,10 2,18" fill="none" stroke="#999" stroke-width="2"/></svg>
<div class="product-tile tile-socks abs" role="img" aria-label="Photo of legs wearing striped teal socks"><span>10%<br>SAVE</span></div>
<div class="product-tile tile-yarn abs" role="img" aria-label="Photo of a ring of colourful yarn balls"></div>

<footer class="footer abs"></footer>
<div class="fcol abs" style="left:125px"><h3>COLLECTIONS</h3><ul><li>Women</li><li>Men</li><li>Baby and Kids</li><li>Home Goods</li><li>Jewelry</li><li>Yarn and Fiber</li><li>Gifts</li><li>Clearance</li></ul></div>
<div class="fcol abs" style="left:301px"><h3>COMPANY</h3><ul><li>About Us</li><li>Affiliates</li><li>Privacy</li><li>Security</li><li>Legal</li><li>Sitemap</li><li>Customer Reviews</li></ul></div>
<div class="fcol abs" style="left:447px"><h3>CUSTOMER SUPPORT</h3><ul><li>· Forgot your password?</li><li>· Visit Customer Service</li></ul>
  <h3 class="gap">SHIPPING &amp; RETURNS</h3><ul><li>· View our Shipping Rates</li><li>· View our Returns Policy</li></ul></div>
<div class="fcol abs" style="left:643px"><h3>CONTACT US</h3><ul><li style="line-height:17.5px">WoolHarbor</li><li style="line-height:17.5px">42 Fernhollow Lane</li><li style="line-height:17.5px">Brackenford</li><li style="line-height:17.5px">BF4 2QT</li><li style="margin-top:10px;line-height:17.5px">Tel: (0) 11 4027 3180</li><li style="line-height:17.5px">Fax: (0) 11 4027 3190</li><li style="margin-top:10px">enquiries@woolharbor.com</li></ul></div>
<div class="fcol abs" style="left:844px"><h3>FEEDBACK</h3>
  <div class="fb-title">Anteposuerit litterarum formas</div><div class="fb-text">Lorem Ipsum est mplement du faux texte employé dans la composition.</div><div class="fb-tag">#ABCD</div>
  <div class="fb-title">Anteposuerit litterarum formas</div><div class="fb-text">Lorem Ipsum est mplement du faux texte employé dans la composition.</div><div class="fb-tag">#ABCD</div>
</div>

<div class="badge abs" style="left:133px;width:87px;height:56px;background:linear-gradient(135deg,#d8c27a,#b89a4c)" aria-label="Gift card"></div>
<div class="badge abs" style="left:288px;top:1078px;width:37px;height:59px;background:#1f5c9a"></div>
<div class="badge abs" style="left:375px;top:1088px;width:124px;height:38px;background:#e6ebf3;border:1px solid #b8c4d8"></div>
<div class="badge abs" style="left:541px;width:51px;height:53px;background:#f2f2f2;border:1px solid #ccc"></div>
<div class="badge abs" style="left:650px;top:1082px;width:94px;height:50px;background:#eef0f4;border-radius:2px"></div>
<div class="badge abs" style="left:796px;top:1081px;width:60px;height:54px;border-radius:50%;background:#d9b640"></div>
<div class="badge abs" style="left:893px;top:1092px;width:126px;height:29px;background:#f2f2f2;border:1px solid #999"></div>

<div class="copyright abs">Copyright 2012 WoolHarbor. All Rights Reserved.</div>
</body>
</html>
```